Large online photo magazine needs redesign

We have previously digitised a historical photographic magazine of around 20,000 printed pages and made it available online. The magazine ran up to the early 1970s, and the content is largely black and white photographs of local events, accompanied by short captions.

Although the content is very rich, the design needs to be revisited so that:
* it is visually appealing
* it is responsive (i.e. works in browsers across all manner of devices)
* is faithful to the nature of the content

There are only a few core page types, and the central one is the article page, an example of which can be seen at:
http://snapgazette.example/gisborne/issue/KLR48_19600714/t1-body-d4.html

Any design submitted should be based on the treatment of an article page such as the above.

Given the large number of pages on our site, we need a design which can be templated to work for any content in the collection, i.e. we cannot hand-craft our templates to match a given page of content, rather a template must work acceptably well for all content.

The current site, although basic in design, has the advantage that it is quite efficient in the amount of data per page request (around 100k - 200k). While not adverse to web fonts, banner imagery etc, we will carefully consider the benefit gained from any such treatment against the amount of extra data that needs to be downloaded to the client's browser.

For the right design, we are able ourselves to adapt it to a CSS layout.

An example of each core page type is as follows (though for this project we only expect a design for a single page, as itemised above):

http://snapgazette.example/gisborne/index.html
http://snapgazette.example/gisborne/about.html
http://snapgazette.example/gisborne/help.html
http://snapgazette.example/gisborne/initial/index.html
http://snapgazette.example/gisborne/search/results?type=section&text=smith&cmdSubmit=Go
http://snapgazette.example/gisborne/advanced-search/index.html
http://snapgazette.example/gisborne/issue/KLR48_19600714/t1-front-d1.html
http://snapgazette.example/gisborne/issue/KLR48_19600714/index.html
http://snapgazette.example/gisborne/issue/KLR48_19600714/fig-KLR48_19600714_005a.html
http://snapgazette.example/gisborne/issue/KLR48_19600714/KLR48_19600714_012.html
http://snapgazette.example/gisborne/issue/KLR48_19600714/thumbnails.html

Target Market(s)

A general browsing audience of all ages, but skewed towards the older generations, and those interested in family / regional history.

The average user will not be particularly web-savy, and the treatment of the content should not detract / distract from the actual content itself.

Industry/Entity Type

Events

Requirements
Must have
• * it is visually appealing
The content should be visually appealing to the audience, which can be defined as a general browsing audience of all ages, but skewed towards the middle and older generations.

* it is responsive (the design can be adapted - by us - to work in browsers across all manner of devices)

The magazine covers (http://snapgazette.example/gisborne/issues/index.html) offer some possible inspiration for treatment of the material.

```html
<!DOCTYPE html>
<html lang="en">
<head>
<meta charset="utf-8">
<title>Snap Gazette – No 73 July 14, 1960</title>
<link rel="stylesheet" href="https://fonts.googleapis.com/css2?family=Open+Sans:wght@400;600;700&display=swap">
<style>
:root{
  --brand:#cc3d52;
  --brand-dark:#b52e43;
  --brand-light:#d9576a;
  --toolbar:#e7e7e7;
  --card-bg:#f8f8f8;
  --card-border:#b9b9b9;
  --text:#555;
  --slate:#4b5661;
  --white:#fff;
}
*{box-sizing:border-box;margin:0;padding:0}
html,body{width:1200px;height:1152px;overflow:hidden}
body{font-family:"Open Sans",Arial,sans-serif;background:var(--white);color:var(--text);position:relative}
a{color:inherit;text-decoration:none}

.site-header{position:absolute;left:0;top:0;width:1200px;height:105px;background:var(--brand)}
.brand{position:absolute;left:112px;top:30px;font-size:38px;font-weight:700;color:var(--white);letter-spacing:1px;display:flex;align-items:center;gap:14px}
.brand-mark{width:18px;height:18px;background:var(--white);border-radius:50%}
.search{position:absolute;left:705px;top:44px;display:flex;align-items:center}
.search label{color:var(--white);font-size:14px;font-weight:600;margin-right:6px}
.search-box{width:192px;height:32px;background:#f1f1f1;border:1px solid #bbb;border-radius:3px;display:flex;align-items:center;font-size:10px;color:#333;padding-left:9px;position:relative}
.search-btn{position:absolute;right:2px;top:2px;width:26px;height:26px;background:linear-gradient(#eee,#c9c9c9);border:1px solid #999;border-radius:3px}

.main-nav{position:absolute;left:0;top:105px;width:1200px;height:40px;background:linear-gradient(var(--brand-light),var(--brand-dark));border-top:1px solid #e06d7f;color:var(--white);font-size:14px;font-weight:600}
.main-nav ul{list-style:none;position:absolute;top:11px;display:flex}
.main-nav li+li::before{content:"|";margin:0 9px}
.nav-left{left:102px}
.nav-right{right:92px}

.toolbar{position:absolute;left:0;top:145px;width:1200px;height:67px;background:var(--toolbar)}
.tool-btn{position:absolute;top:13px;width:130px;height:34px;border-radius:4px;background:linear-gradient(#3a3a3a,#0e0e0e);border:1px solid #666;box-shadow:0 1px 2px rgba(0,0,0,.4);color:var(--white);font-size:13px;font-weight:700;display:flex;align-items:center;justify-content:center}
.tool-btn svg{position:absolute;top:0}
.printer{position:absolute;left:1040px;top:8px}

.issue-title{position:absolute;left:127px;top:236px;font-size:27px;color:var(--brand);font-weight:400}
.view-page{position:absolute;left:931px;top:241px;width:124px;height:39px;background:linear-gradient(#f4f4f4,#dcdcdc);clip-path:polygon(0 0,88% 0,100% 50%,88% 100%,0 100%);color:#8a8a8a;font-size:13px;font-weight:600;display:flex;align-items:center;padding-left:24px}

.story{position:absolute;width:937px;height:219px;background:var(--card-bg);border:1px solid var(--card-border);box-shadow:2px 2px 4px rgba(0,0,0,.25)}
.story-photo{position:absolute;left:0;top:0;width:194px;height:217px}
.story h2{position:absolute;left:215px;top:12px;font-size:23px;font-weight:700;color:var(--brand);letter-spacing:.3px}
.story p{position:absolute;left:216px;right:26px;font-size:15.5px;line-height:21px;color:#555;text-align:justify}
.read-more{position:absolute;left:218px;width:117px;height:33px;border-radius:4px;background:linear-gradient(#e0586b,#b72c41);border:1px solid #a3293b;color:var(--white);font-size:15px;display:flex;align-items:center;justify-content:center}
.share-bar{position:absolute;left:496px;width:428px;height:38px;background:var(--white);display:flex;align-items:center;font-size:11px}
.share{display:flex;align-items:center;position:absolute}
.share-btn{height:19px;padding:0 5px;border-radius:2px;display:flex;align-items:center;gap:4px;font-weight:600}
.share-btn i{display:block;width:9px;height:9px}
.share-count{height:19px;min-width:22px;border:1px solid #ccc;margin-left:4px;display:flex;align-items:center;justify-content:center;color:#555;font-size:10px;background:#fff}
.like .share-btn{background:#4a67a6;color:#fff}
.like i{background:#fff}
.post .share-btn{background:#f2f2f2;border:1px solid #ccc;color:#333}
.post i{background:#4aa3df}
.plus .share-btn{background:#f2f2f2;border:1px solid #ccc;color:#d34836}
.plus i{background:#d34836}
.shr .share-btn{background:#f26b3a;color:#fff}
.shr i{background:#fff}
.shr .share-count{min-width:36px;font-weight:700;color:#333}

.pager-band{position:absolute;left:0;top:1010px;width:1200px;height:66px;background:var(--toolbar)}
.pager{position:absolute;top:19px;left:416px;display:flex;gap:10px;list-style:none}
.pager li{height:30px;min-width:30px;padding:0 8px;background:linear-gradient(#5c6873,#3e4851);border:1px solid #2e363d;color:#fff;font-size:14px;font-weight:700;display:flex;align-items:center;justify-content:center}
.pager li.wide{width:60px}
.pager li.current{background:var(--brand)}

.site-footer{position:absolute;left:0;top:1076px;width:1200px;height:76px;background:var(--brand);color:var(--white)}
.copyright{position:absolute;left:113px;top:26px;font-size:14px}
.licence{position:absolute;left:577px;top:22px;width:88px;height:31px;background:#fff;border:2px solid #000}
.licence span{position:absolute;left:2px;right:2px;bottom:2px;height:7px;background:#000}
.social{position:absolute;left:873px;top:18px;display:flex;gap:8px;list-style:none}
.social li{width:38px;height:38px;border-radius:50%;background:radial-gradient(#f7f7f7,#d4d4d4);border:3px solid #a9323f;box-shadow:0 0 0 1px #e57a89}
</style>
</head>
<body>

<header class="site-header">
  <a class="brand" href="http://snapgazette.example/gisborne/index.html"><span class="brand-mark"></span>Snap Gazette</a>
  <form class="search">
    <label>Search Snap Gazette</label>
    <div class="search-box">Search<span class="search-btn"></span></div>
  </form>
</header>

<nav class="main-nav">
  <ul class="nav-left">
    <li><a href="http://snapgazette.example/gisborne/index.html">Home</a></li>
    <li><a href="http://snapgazette.example/gisborne/about.html">About</a></li>
    <li><a href="http://snapgazette.example/gisborne/issues/index.html">Browse Snap Gazette</a></li>
    <li><a href="http://snapgazette.example/gisborne/initial/index.html">A-Z people</a></li>
  </ul>
  <ul class="nav-right">
    <li><a href="http://snapgazette.example/gisborne/advanced-search/index.html">Advanced search</a></li>
    <li><a href="http://snapgazette.example/gisborne/help.html">Help</a></li>
    <li><a href="#">Report an error</a></li>
  </ul>
</nav>

<div class="toolbar">
  <a class="tool-btn" style="left:104px;padding-left:28px">PREVIOUS
    <svg style="left:4px" width="30" height="34" viewBox="0 0 30 34"><rect width="30" height="34" rx="3" fill="#555"/><path d="M16 11l-6 6 6 6M23 11l-6 6 6 6" stroke="#fff" stroke-width="2.5" fill="none"/></svg></a>
  <a class="tool-btn" style="left:245px;padding-right:26px" href="http://snapgazette.example/gisborne/issue/KLR48_19600714/index.html">ISSUE
    <svg style="right:2px" width="28" height="34" viewBox="0 0 28 34"><rect width="28" height="34" rx="3" fill="#555"/><path d="M14 9l-6 7h4v9h4v-9h4z" fill="#fff"/></svg></a>
  <a class="tool-btn" style="left:386px;padding-right:28px">NEXT
    <svg style="right:2px" width="30" height="34" viewBox="0 0 30 34"><rect width="30" height="34" rx="3" fill="#555"/><path d="M8 11l6 6-6 6M15 11l6 6-6 6" stroke="#fff" stroke-width="2.5" fill="none"/></svg></a>
  <svg class="printer" width="58" height="46" viewBox="0 0 58 46" aria-label="Print">
    <rect x="14" y="2" width="30" height="16" fill="#fff" stroke="#888"/>
    <rect x="3" y="15" width="52" height="22" rx="4" fill="#9a9a9a" stroke="#666"/>
    <rect x="12" y="30" width="34" height="14" fill="#fff" stroke="#888"/>
    <rect x="44" y="20" width="6" height="3" fill="#5c5"/>
  </svg>
</div>

<main>
  <h1 class="issue-title">No 73 July 14, 1960</h1>
  <a class="view-page" href="http://snapgazette.example/gisborne/issue/KLR48_19600714/KLR48_19600714_012.html">VIEW PAGE</a>

  <article class="story" style="left:126px;top:295px">
    <div class="story-photo" role="img" aria-label="Photograph of three sisters in air hostess uniforms, with printed caption beneath" style="background:linear-gradient(#8b8574,#c9c3b0 60%,#e4dfcf)"></div>
    <h2>FLYING SISTERS FROM GISBORNE</h2>
    <p style="top:45px">This is probably something of a record--three sisters who are all air hostesses. They are the Marsden sisters.....Colette, Ilse, and Lorraine, daughters of Mr and Mrs R. T. Marsden,<br><br>This is probably something of a record--three sisters who are all air hostesses. They are the Marsden sisters</p>
    <a class="read-more" style="top:162px" href="http://snapgazette.example/gisborne/issue/KLR48_19600714/t1-body-d4.html">READ MORE</a>
    <div class="share-bar" style="top:157px">
      <span class="share like" style="left:17px"><span class="share-btn"><i></i>Like</span><span class="share-count">5</span></span>
      <span class="share post" style="left:105px"><span class="share-btn"><i></i>Post</span><span class="share-count">10</span></span>
      <span class="share plus" style="left:224px"><span class="share-btn"><i></i>+1</span><span class="share-count">4</span></span>
      <span class="share shr" style="left:323px"><span class="share-btn"><i></i>Share</span><span class="share-count">4</span></span>
    </div>
  </article>

  <article class="story" style="left:127px;top:536px">
    <div class="story-photo" role="img" aria-label="Photograph of an air hostess stepping from an aircraft doorway" style="background:linear-gradient(135deg,#4a463d,#9c9684 55%,#d8d2bf)"></div>
    <h2 style="left:220px">PERSONAL</h2>
    <p style="top:49px;left:219px">These are the members of the No. 2 Starlite Show Band, now entertaining at Surfers Paradise, Queensland, The band includes two Gisborne members. From left, Dennis Hale (Rotorua), Tom Waaka (Gisborne), Ted Rangi (Gisborne), Johnny Brooks (Waikato), Martin Keane (North Auckland), and Graham Walsh (Invercargill). Their vocalist is Carla Dean.</p>
    <a class="read-more" style="top:153px;left:221px" href="http://snapgazette.example/gisborne/issue/KLR48_19600714/t1-body-d4.html">READ MORE</a>
    <div class="share-bar" style="top:157px">
      <span class="share like" style="left:17px"><span class="share-btn"><i></i>Like</span><span class="share-count">5</span></span>
      <span class="share post" style="left:105px"><span class="share-btn"><i></i>Post</span><span class="share-count">10</span></span>
      <span class="share plus" style="left:224px"><span class="share-btn"><i></i>+1</span><span class="share-count">4</span></span>
      <span class="share shr" style="left:323px"><span class="share-btn"><i></i>Share</span><span class="share-count">4</span></span>
    </div>
  </article>

  <article class="story" style="left:131px;top:775px">
    <div class="story-photo" role="img" aria-label="Photograph of an old truss bridge across a river, with printed caption" style="background:linear-gradient(#d6d1c0,#a9a393 45%,#6d685b 55%,#cfc9b6)"></div>
    <h2>FLYING SISTERS FROM GISBORNE</h2>
    <p style="top:52px">The old highway bridge across the Waiapu River near Ruatoria probably has more Bailey "splints" than any other bridge in the country. It is to be replaced soon by a modern structure two miles downstream, after which all main-route traffic will pass through Ruatoria township. (Picture, Eastland).</p>
    <a class="read-more" style="top:162px" href="http://snapgazette.example/gisborne/issue/KLR48_19600714/t1-body-d4.html">READ MORE</a>
    <div class="share-bar" style="top:157px">
      <span class="share like" style="left:17px"><span class="share-btn"><i></i>Like</span><span class="share-count">5</span></span>
      <span class="share post" style="left:105px"><span class="share-btn"><i></i>Post</span><span class="share-count">10</span></span>
      <span class="share plus" style="left:224px"><span class="share-btn"><i></i>+1</span><span class="share-count">4</span></span>
      <span class="share shr" style="left:323px"><span class="share-btn"><i></i>Share</span><span class="share-count">4</span></span>
    </div>
  </article>
</main>

<nav class="pager-band">
  <ul class="pager">
    <li class="wide">Prev</li><li class="current">1</li><li>2</li><li>3</li><li>4</li><li>5</li><li>6</li><li>…</li><li>22</li><li class="wide">Next</li>
  </ul>
</nav>

<footer class="site-footer">
  <p class="copyright">© 2012 Harbourside Memorial Library</p>
  <div class="licence" role="img" aria-label="Licence badge"><span></span></div>
  <ul class="social"><li></li><li></li><li></li><li></li><li></li></ul>
</footer>

</body>
</html>
```